Design a web site for my business - Brightline Coatings Co.

We are a family business that handles design, fabrication and installation of powder coated aluminum, stainless steel and glass products. Including handrails, privacy slat screens, electric gates and pool fencing. We are based in the Whitsundays in North Queensland and service an area from Airlie Beach to Townsville.

Target Market(s)

Domestic and commercial

Industry/Entity Type

fabrication - manufacturing

Coding

Coded - Design and coding required

Number of Pages Required

5+ page

Colors
0054AA
0677BA
7BADD7
CADEEF
E8F1F8

Requirements
Must have
• photo galleries, contact page, one page for privacy screens, balustrades, glass fencing, stainless steel handrail, powder coated aluminium handrails and pool fencing

```html
<!DOCTYPE html>
<html lang="en">
<head>
<meta charset="utf-8">
<title>Contact — Brightline Coatings Co</title>
<link href="https://fonts.googleapis.com/css2?family=Inter:wght@400;500;600;700;800&display=swap" rel="stylesheet">
<style>
:root{
  --blue:#0054AA;
  --blue-mid:#0677BA;
  --blue-soft:#7BADD7;
  --blue-pale:#CADEEF;
  --blue-mist:#E8F1F8;
  --page:#f7fafd;
  --ink:#0a1f3d;
  --text:#3d5573;
  --muted:#5b7391;
  --line:#b9d1e8;
  --white:#ffffff;
  --footer:#062a55;
  --footer-text:#9fbfdf;
  --footer-body:#d6e6f4;
  --footer-line:#1b4478;
}
*{box-sizing:border-box;margin:0;padding:0}
html,body{width:821px;height:1200px;overflow:hidden}
body{position:relative;background:var(--page);font-family:"Inter",sans-serif;color:var(--ink)}
.abs{position:absolute}

/* header */
.site-header{left:0;top:0;width:821px;height:62px;border-bottom:1px solid var(--blue-pale);background:var(--white)}
.brand{left:41px;top:20px;display:flex;align-items:center;gap:6px;font-size:10px;font-weight:700;color:var(--blue)}
.brand-mark{width:12px;height:12px;background:var(--blue)}
.main-nav{left:240px;top:23px;display:flex;gap:20.5px;font-size:11px;color:var(--text)}
.main-nav .active{color:var(--blue);font-weight:600;border-bottom:1.5px solid var(--blue);padding-bottom:3px;margin-top:-2px}
.quote-btn{left:657px;top:16.5px;width:123px;height:28px;background:var(--blue);color:var(--white);border-radius:5px;font-size:8.5px;font-weight:700;letter-spacing:.6px;display:flex;align-items:center;justify-content:center}

/* intro */
.eyebrow{left:41px;top:103px;font-size:7.7px;font-weight:700;letter-spacing:1.6px;color:var(--blue-mid)}
.page-title{left:41px;top:123px;font-size:31px;font-weight:700;letter-spacing:-.6px;color:var(--ink)}
.intro{left:41px;top:175px;width:440px;font-size:11.5px;line-height:18.6px;color:var(--text)}

/* form */
.quote-form{left:41px;top:254px;width:482px;height:550px;background:var(--white);border:1px solid var(--line);border-radius:4px}
.field-label{font-size:7.5px;font-weight:700;letter-spacing:1px;color:var(--ink)}
.field{border:1px solid var(--line);background:var(--white);font-size:10.2px;color:#9bb0c6;padding-left:4px;display:flex;align-items:center}
.field.select{color:var(--ink);justify-content:space-between;padding-right:5px}
.field.area{align-items:flex-start;padding:11px 10px}
.submit-btn{left:72.5px;top:650px;width:192px;height:41px;background:var(--blue);color:var(--white);border-radius:5px;font-size:10.5px;font-weight:700;display:flex;align-items:center;justify-content:center;gap:8px}

/* contact info */
.info-card{left:554px;top:254px;width:226px;height:287px;background:var(--blue-mist);border:1px solid var(--blue-pale);border-radius:4px}
.info-title{left:575px;top:276px;font-size:15.5px;font-weight:500;color:var(--ink)}
.rule{height:1px;background:var(--blue-pale)}
.icon-box{width:29.5px;height:29.5px;background:var(--white);border-radius:5px;display:flex;align-items:center;justify-content:center}
.info-label{font-size:7.5px;font-weight:700;letter-spacing:1px;color:var(--muted)}
.badge{left:575px;top:455px;width:184px;height:65px;border:1px solid var(--blue-pale);background:var(--white);display:flex;align-items:center;gap:9px;padding-left:13px}
.badge strong{display:block;font-size:10px;line-height:12.5px;font-weight:700;color:var(--ink)}
.badge small{display:block;font-size:7.5px;letter-spacing:.7px;color:var(--muted);margin-top:4px}

/* map */
.map-card{left:554px;top:562px;width:226px;height:224px;border:1px solid var(--blue-pale);border-radius:4px;overflow:hidden}
.map-fill{position:absolute;inset:0;background:linear-gradient(135deg,var(--blue-mist) 0%,var(--blue-pale) 55%,#b3cfe8 100%)}
.area-card{left:571px;top:680px;width:192px;height:90px;background:var(--white);border-radius:4px;box-shadow:0 3px 10px rgba(0,60,120,.14);padding:15px 15.5px}
.area-card h3{font-size:7.8px;font-weight:800;letter-spacing:1.6px;margin-bottom:5px;color:var(--blue)}
.area-card p{font-size:8.8px;line-height:14.7px;color:var(--text)}

/* footer */
.site-footer{left:0;top:845px;width:821px;height:355px;background:var(--footer)}
.footer-brand{left:41px;top:897px;width:64px;height:51px;background:var(--blue-mist);display:flex;align-items:center;justify-content:center;text-align:center;font-size:8px;font-weight:700;line-height:10px;color:var(--blue)}
.footer-about{left:41px;top:973px;width:250px;font-size:11.5px;line-height:19px;color:var(--footer-body)}
.social{width:25.5px;height:25.5px;border:1px solid var(--footer-line);border-radius:5px;display:flex;align-items:center;justify-content:center}
.col-head{font-size:7.7px;font-weight:700;letter-spacing:1.2px;color:var(--blue-soft)}
.col-list{list-style:none;font-size:10.3px;color:var(--footer-body)}
.col-list li{height:25.7px}
.news-text{left:618px;top:928px;width:162px;font-size:8.8px;line-height:12.8px;color:var(--footer-text)}
.news-input{left:618px;top:969px;width:162px;height:30px;background:#0a3566;border:1px solid var(--footer-line);border-radius:2px;font-size:8.8px;color:#86a9cc;padding-left:11px;display:flex;align-items:center}
.subscribe{left:618px;top:1006px;width:162px;height:28px;background:var(--blue-mist);border-radius:2px;font-size:8.8px;font-weight:700;letter-spacing:.7px;display:flex;align-items:center;justify-content:center;color:var(--blue)}
.footer-rule{left:41px;top:1135px;width:739px;height:1px;background:var(--footer-line)}
.legal{top:1162px;font-size:9px;color:var(--footer-text)}
</style>
</head>
<body>

<header class="abs site-header"></header>
<div class="abs brand"><span class="brand-mark"></span>Brightline Coatings Co</div>
<nav class="abs main-nav"><span>Services</span><span>Projects</span><span>Areas</span><span>About</span><span class="active">Contact</span></nav>
<div class="abs quote-btn">REQUEST QUOTE</div>

<p class="abs eyebrow">GET IN TOUCH</p>
<h1 class="abs page-title">Let's Build Something Together</h1>
<p class="abs intro">From Airlie Beach to Townsville, we provide precision aluminium and steel fabrication for coastal properties. Discuss your project with our expert team.</p>

<section class="abs quote-form"></section>
<span class="abs field-label" style="left:72.5px;top:286px">NAME</span>
<div class="abs field" style="left:72.5px;top:300px;width:199.5px;height:31px">Your full name</div>
<span class="abs field-label" style="left:292.5px;top:286px">PHONE</span>
<div class="abs field" style="left:292.5px;top:300px;width:199.5px;height:31px">Best contact number</div>
<span class="abs field-label" style="left:72.5px;top:353px">EMAIL</span>
<div class="abs field" style="left:72.5px;top:367px;width:419.5px;height:31px">email@example.com</div>
<span class="abs field-label" style="left:72.5px;top:419px">SERVICE NEEDED</span>
<div class="abs field select" style="left:72.5px;top:434px;width:199.5px;height:31px">Select a service
  <svg width="9" height="6" viewBox="0 0 9 6"><path d="M1 1l3.5 3.5L8 1" fill="none" stroke="#0054AA" stroke-width="1"/></svg></div>
<span class="abs field-label" style="left:292.5px;top:419px">LOCATION</span>
<div class="abs field select" style="left:292.5px;top:434px;width:199.5px;height:31px">Select your area
  <svg width="9" height="6" viewBox="0 0 9 6"><path d="M1 1l3.5 3.5L8 1" fill="none" stroke="#0054AA" stroke-width="1"/></svg></div>
<span class="abs field-label" style="left:72.5px;top:486px">PROJECT DESCRIPTION</span>
<div class="abs field area" style="left:72.5px;top:505px;width:419.5px;height:114px">Please describe dimensions, materials, and specific requirements...</div>
<div class="abs submit-btn">Submit Quote Request
  <svg width="11" height="10" viewBox="0 0 11 10"><path d="M1 5h8.5M6 1.5L9.5 5 6 8.5" fill="none" stroke="#fff" stroke-width="1.4"/></svg></div>

<aside class="abs info-card"></aside>
<h2 class="abs info-title">Contact Info</h2>
<div class="abs rule" style="left:575px;top:305px;width:184px"></div>
<div class="abs icon-box" style="left:575px;top:326px">
  <svg width="12" height="12" viewBox="0 0 24 24"><path d="M6.6 10.8a15 15 0 006.6 6.6l2.2-2.2a1 1 0 011-.25 11.4 11.4 0 003.6.57 1 1 0 011 1V20a1 1 0 01-1 1A17 17 0 013 4a1 1 0 011-1h3.5a1 1 0 011 1c0 1.25.2 2.45.57 3.57a1 1 0 01-.25 1z" fill="#0054AA"/></svg></div>
<span class="abs info-label" style="left:617.5px;top:328px">CALL US</span>
<span class="abs" style="left:617.5px;top:341.5px;font-size:11.5px;color:var(--ink)">0400 118 552</span>
<div class="abs icon-box" style="left:575px;top:378px">
  <svg width="12" height="10" viewBox="0 0 24 18"><rect x="0" y="0" width="24" height="18" rx="2" fill="#0054AA"/><path d="M2 3l10 7 10-7" fill="none" stroke="#fff" stroke-width="2"/></svg></div>
<span class="abs info-label" style="left:617.5px;top:379px">EMAIL US</span>
<span class="abs" style="left:617.5px;top:393px;font-size:9.5px;color:var(--ink)">hello@brightlinecoat.com.au</span>
<div class="abs rule" style="left:575px;top:429px;width:184px"></div>
<div class="abs badge">
  <svg width="17" height="17" viewBox="0 0 24 24"><path d="M12 1l2.8 2.2 3.5-.4.9 3.4 3 1.9-1.3 3.3 1.3 3.3-3 1.9-.9 3.4-3.5-.4L12 23l-2.8-2.2-3.5.4-.9-3.4-3-1.9L3.1 12 1.8 8.7l3-1.9.9-3.4 3.5.4z" fill="#0677BA"/><path d="M7.5 12l3 3 6-6" fill="none" stroke="#fff" stroke-width="2"/></svg>
  <div><strong>Family Owned &amp;<br>Operated</strong><small>LOCAL QLD CRAFTSMANSHIP</small></div>
</div>

<div class="abs map-card"><div class="map-fill" role="img" aria-label="Map of the service area from Airlie Beach to Bowen and Townsville"></div></div>
<div class="abs area-card"><h3>SERVICE AREA</h3><p>Serving Airlie Beach, Bowen, Townsville, and all surrounding Whitsunday regions.</p></div>

<footer class="abs site-footer"></footer>
<div class="abs footer-brand">Brightline<br>Coatings Co</div>
<p class="abs footer-about">Precision Craftsmanship for the Coast. We specialize in bespoke metalwork solutions that withstand the tropical Queensland climate.</p>
<div class="abs social" style="left:41px;top:1068.5px">
  <svg width="9" height="9" viewBox="0 0 24 24" fill="none" stroke="#E8F1F8" stroke-width="2.2"><circle cx="18" cy="5" r="3"/><circle cx="6" cy="12" r="3"/><circle cx="18" cy="19" r="3"/><path d="M8.6 13.5l6.8 4M15.4 6.5l-6.8 4"/></svg></div>
<div class="abs social" style="left:77px;top:1068.5px">
  <svg width="9" height="9" viewBox="0 0 24 24" fill="none" stroke="#E8F1F8" stroke-width="2.2"><path d="M12 22s7-6.5 7-12a7 7 0 00-14 0c0 5.5 7 12 7 12z"/><circle cx="12" cy="10" r="2.5"/></svg></div>

<span class="abs col-head" style="left:362px;top:899px">SERVICES</span>
<ul class="abs col-list" style="left:362px;top:929px"><li>Handrails</li><li>Privacy Screens</li><li>Electric Gates</li><li>Pool Fencing</li><li>Glass Balustrades</li></ul>
<span class="abs col-head" style="left:490px;top:899px">AREAS</span>
<ul class="abs col-list" style="left:490px;top:929px"><li>Airlie Beach</li><li>Bowen</li><li>Townsville</li></ul>
<span class="abs col-head" style="left:618px;top:899px">NEWSLETTER</span>
<p class="abs news-text">Stay updated with our latest projects and news.</p>
<div class="abs news-input">Enter your email</div>
<div class="abs subscribe">SUBSCRIBE</div>

<div class="abs footer-rule"></div>
<span class="abs legal" style="left:41px">© 2024 Brightline Coatings Co. Precision Craftsmanship for the Coast.</span>
<span class="abs legal" style="left:628px">Privacy Policy</span>
<span class="abs legal" style="left:707.5px">Terms of Service</span>

</body>
</html>
```